sydney wedding photography business needs a business card design

we need a business card design for a sydney based wedding photography and videography business. our business name is :golden hour studio and film. our target clients are 24-35 yrs female. our style is candid, organic, natural, dynamic. we are a team of young photographers and videographers, and help brides to create memories that they will cherish for the rest of their lives. the logo will be provided. we want an elegant design that reflects our style, and also want to give a great impression to our clients that we are one of the best studios in sydney and our brand means quality and premium service.

Target Market(s)

bride to be, 24-35 years old, living in sydney and surrunding areas

Industry/Entity Type

Wedding Photography

Contact Information for Business Card

address: 57 tarrant street, glenmore nsw 2047
mobile: 0431872259
phone: (02) 9163 2408
info@tidewillowstudio.net.au
www.tidewillowstudio.net.au
facebook:tidewillowweddings
instagram:tidewillowweddings

Font styles to use
Serif
Sans Serif

Requirements
Nice to have
• maybe add my slogan"memories beyond eternity" if the layout looks good
Should not have
• no black color, not good idea for wedding biz card

```html
<!DOCTYPE html>
<html lang="en">
<head>
<meta charset="utf-8">
<title>Golden Hour Studio and Film – Business Card</title>
<link rel="stylesheet" href="https://fonts.googleapis.com/css2?family=Mulish:wght@400;600&display=swap">
<style>
  :root {
    --backdrop: #ece7dd;
    --card: #3b2c22;
    --card-glow: #4a382b;
    --gold: #e5b21a;
    --ink-light: #f3eee4;
    --rule: #7a6654;
  }
  * { margin: 0; padding: 0; box-sizing: border-box; }
  html, body { width: 1200px; height: 774px; overflow: hidden; }
  body {
    background: var(--backdrop);
    font-family: "Mulish", Arial, sans-serif;
    position: relative;
  }
  .card {
    position: absolute;
    top: 232px;
    width: 540px;
    height: 310px;
    background: var(--card);
    overflow: hidden;
  }
  .card--front { left: 45px; }
  .card--back { left: 615px; }

  /* Front */
  .brand-name {
    position: absolute;
    top: 98px;
    left: 0;
    width: 100%;
    text-align: center;
    color: var(--gold);
    font-weight: 600;
    font-size: 40px;
    letter-spacing: 1px;
    line-height: 1.15;
  }
  .brand-name span {
    display: block;
    font-size: 14px;
    letter-spacing: 8px;
    text-transform: uppercase;
    margin-top: 6px;
  }
  .front-rule {
    position: absolute;
    left: 24px;
    right: 24px;
    top: 250px;
    border-top: 1px solid var(--rule);
  }
  .social {
    position: absolute;
    top: 263px;
    display: flex;
    align-items: center;
    gap: 8px;
    color: var(--ink-light);
    font-size: 13px;
    letter-spacing: 0.3px;
    text-transform: uppercase;
  }
  .social--left { left: 24px; }
  .social--right { right: 24px; }
  .social-dot {
    width: 15px;
    height: 15px;
    border-radius: 50%;
    background: var(--gold);
  }

  /* Back */
  .pattern-field {
    position: absolute;
    inset: 0;
    background: radial-gradient(circle at 50% 60%, var(--card-glow), var(--card));
  }
  .contact {
    position: absolute;
    left: 0;
    top: 112px;
    width: 100%;
    text-align: center;
    color: var(--ink-light);
    font-size: 15px;
    line-height: 1.55;
    letter-spacing: 0.2px;
    text-transform: uppercase;
  }
  .contact-mark {
    width: 28px;
    height: 28px;
    border-radius: 50%;
    border: 4px solid var(--gold);
    margin: 0 auto 12px;
  }
  .contact-name { font-size: 19px; }
  .contact-name .person { color: var(--gold); font-weight: 600; }
  .label { color: var(--gold); font-weight: 600; }
</style>
</head>
<body>
  <section class="card card--front" aria-label="Card front">
    <div class="brand-name">Golden Hour<span>Studio and Film</span></div>
    <div class="front-rule"></div>
    <div class="social social--left"><i class="social-dot"></i>tidewillowweddings</div>
    <div class="social social--right">tidewillowweddings<i class="social-dot"></i></div>
  </section>

  <section class="card card--back" aria-label="Card back">
    <div class="pattern-field" role="img" aria-label="Faint repeating ring pattern across the card"></div>
    <div class="contact">
      <div class="contact-mark"></div>
      <p class="contact-name"><span class="person">Mara Ellison</span> – CEO/Founder</p>
      <p>57 Tarrant Street, Glenmore NSW 2047</p>
      <p><span class="label">Phone :</span> (02) 9163 2408 <span class="label">Cell :</span> (04) 3187 2259</p>
      <p>info@tidewillowstudio.net.au | www.tidewillowstudio.net.au</p>
    </div>
  </section>
</body>
</html>
```